Sea Shipping Logistics Company

The business is a logistics company (sea shipping and other special logistics) and also sales of bulk building materials.
The Design should be minimalistic and give a feeling of power and connectivity.
When the client sees the card, they should get a feeling of confident. Dark overall color (background) and print should be red / white .See logo. The card will be printed on trifecta with the middle color being red.

One side should be the logo and a 5 / 6 word slogan
And other side name, contact (phone/email) and a QR Code.

Target Market(s)

Construction companies / Oil & Gas related companies

Industry/Entity Type

Sea Bulk Shipping Logistics

Contact Information for Business Card

Name, Telephone number, Email address, Website URL, QR Code (see description)

Font styles to use
Sans Serif

Requirements
Must have
• No idea
Nice to have
• Minimalistic, but strong and powerful look and feel.

```html
<!DOCTYPE html>
<html lang="en">
<head>
<meta charset="utf-8">
<title>KOLDA business card</title>
<link href="https://fonts.googleapis.com/css2?family=Archivo:wght@800&family=Roboto:wght@400&display=swap" rel="stylesheet">
<style>
  :root {
    --backdrop: #232020;
    --brand-red: #cc0022;
    --paper: #eeeef0;
    --ink: #111111;
    --steel: #6a6a6a;
    --white: #ffffff;
  }
  html, body { margin: 0; padding: 0; overflow: hidden; }
  .canvas {
    position: relative; width: 1200px; height: 1200px;
    background: var(--backdrop); overflow: hidden;
    font-family: "Roboto", Arial, sans-serif;
  }
  .card { position: absolute; width: 594px; height: 350px; border-radius: 22px; overflow: hidden; }
  .card--front { left: 298px; top: 198px; background: var(--brand-red); }
  .card--back { left: 292px; top: 637px; background: var(--paper); }

  .brand { position: absolute; display: flex; align-items: center; }
  .brand__square { border: 3px solid var(--ink); box-sizing: border-box; }
  .brand__name { font-family: "Archivo", Arial, sans-serif; font-weight: 800; line-height: 1; letter-spacing: -1px; }

  .card--front .brand { left: 120px; top: 104px; gap: 14px; }
  .card--front .brand__square { width: 129px; height: 116px; }
  .card--front .brand__name { font-size: 68px; color: var(--steel); }

  .services {
    position: absolute; left: 0; right: 0; top: 294px; margin: 0; text-align: center;
    color: var(--white); font-size: 15px; line-height: 20px; letter-spacing: 1px; word-spacing: 2px;
  }
  .services__divider { display: inline-block; margin: 0 10px; }

  .card--back .brand { left: 48px; top: 71px; flex-direction: column; gap: 12px; width: 210px; }
  .card--back .brand__square { width: 114px; height: 102px; }
  .card--back .brand__name { font-size: 60px; color: var(--ink); }

  .person { position: absolute; left: 312px; top: 72px; color: var(--ink); }
  .person__name { font-family: "Archivo", Arial, sans-serif; font-weight: 800; font-size: 27px; color: var(--brand-red); line-height: 1; }
  .person__role { font-size: 16px; margin-top: 5px; }

  .contact { position: absolute; left: 312px; top: 156px; margin: 0; padding: 0; list-style: none; font-size: 16px; color: var(--ink); }
  .contact__item { display: flex; align-items: center; height: 22px; }
  .contact__icon { width: 14px; height: 14px; margin-right: 16px; fill: var(--brand-red); }
  .contact__address { margin-top: 6px; }
  .contact__accent { color: var(--brand-red); }

  .sector-band { position: absolute; left: 0; top: 0; width: 594px; height: 350px; }
  .sector-label { position: absolute; left: 312px; top: 317px; color: var(--white); font-size: 16px; }
</style>
</head>
<body>
<main class="canvas">

  <section class="card card--front" aria-label="Card front">
    <div class="brand">
      <div class="brand__square"></div>
      <span class="brand__name">KOLDA</span>
    </div>
    <p class="services">PARTS<span class="services__divider">|</span>TRANSPORT<span class="services__divider">|</span>MECHANIX</p>
  </section>

  <section class="card card--back" aria-label="Card back">
    <div class="brand">
      <div class="brand__square"></div>
      <span class="brand__name">KOLDA</span>
    </div>

    <div class="person">
      <div class="person__name">MARK DALEN</div>
      <div class="person__role">Managing Director</div>
    </div>

    <ul class="contact">
      <li class="contact__item">
        <svg class="contact__icon" viewBox="0 0 16 16"><path d="M1 5c0-2 3-3 7-3s7 1 7 3v1h-4V5H5v1H1zM3 7h10l1 7H2z"/></svg>
        +597 610-2398
      </li>
      <li class="contact__item">
        <svg class="contact__icon" viewBox="0 0 16 16"><path d="M1 3h14v10H1z M2 4l6 5 6-5" fill="var(--brand-red)" stroke="var(--white)" stroke-width="1.2"/></svg>
        info@kolda-transport.com
      </li>
      <li class="contact__item">
        <svg class="contact__icon" viewBox="0 0 16 16"><circle cx="8" cy="8" r="7"/><path d="M1 8h14M8 1v14M3 4h10M3 12h10" stroke="var(--white)" stroke-width="0.9" fill="none"/></svg>
        www.<span class="contact__accent">kolda</span>-transport.com
      </li>
      <li class="contact__address">Kadeweg 14, Noordhaven</li>
    </ul>

    <svg class="sector-band" viewBox="0 0 594 350" aria-hidden="true">
      <path d="M282 307 H594 V350 H254 Z" fill="var(--brand-red)"/>
    </svg>
    <span class="sector-label">Sea Bulk Shipping Logistics</span>
  </section>

</main>
</body>
</html>
```